Exclusive beauty salon needs a price list or services booklet

I need a new very attractive flyer for my beauty salon, containing information on the different services and their prices.
In attachment you can find a pdf of the "old" one, but I'd love to have a beautifully designed new one!
I'd love to have a booklet in format 148 x 148 mm, or in US format, containing 12 or 16 pages, but if you can offer other nice looking designs they are welcome!
The services that need to come in the booklet with their prices can all be found on my website: www.atelierverano.be, starting with
Gelaatsverzorging
Wimperverlenging
Suikerontharing
Wimperlifting
Permanente Make Up
Airbrush Tanning

Target Market(s)

woman from 20 to 89 years old

Industry/Entity Type

Beauty Salon

Font styles to use
Sans Serif

Colors

Designer to choose colors to be used in the design.

Requirements
Must have
• a classy nice look, it must contain details about the services from my beauty salon and their prices, and nice pictures.
• The Names, prices and explanations of the services can easily be found on my website: www.atelierverano.be
Nice to have
• In attachment you can find the "old" price list in pdf, what I need now is a "new booklet" with the new logo and updated services price list.
• I need a very nice and attractive looking booklet, classy chique, Paris chique, looking very expensive.
Should not have
• Not too much colors, not too curly, but still feminine

```html
<!DOCTYPE html>
<html lang="nl">
<head>
<meta charset="utf-8">
<title>Atelier Verano – Prijslijst</title>
<link rel="stylesheet" href="https://fonts.googleapis.com/css2?family=Questrial&family=Nunito:wght@600;700&display=swap">
<style>
  :root {
    --stage: #ecebea;
    --ink: #1d1d1d;
    --ink-soft: #333;
    --blush: #f7dde2;
    --blush-deep: #f3c9d2;
    --sky: #cfe6ee;
    --sky-bar: #a9dbe9;
    --peach: #f7d6c6;
    --peach-light: #fbe9df;
    --teal: #4fbfc9;
    --rose-pill: #ee9ea8;
    --ring: #a6d9e6;
    --white: #ffffff;
  }
  * { box-sizing: border-box; margin: 0; padding: 0; }
  html, body { width: 1200px; height: 1200px; overflow: hidden; }
  body { background: var(--stage); position: relative; font-family: "Questrial", sans-serif; color: var(--ink); }

  .panel { position: absolute; width: 505px; height: 505px; overflow: hidden; box-shadow: 0 6px 18px rgba(0,0,0,.18); background: var(--white); }
  .panel--front { left: 97px; top: 78px; }
  .panel--back { left: 637px; top: 78px; }
  .panel--inside { left: 334px; top: 667px; }

  /* front */
  .front-bg { position: absolute; inset: 0; }
  .portrait-circle { position: absolute; left: 106px; top: 70px; width: 296px; height: 296px; border-radius: 50%;
    background: radial-gradient(circle at 50% 45%, #f1d9cd 0 38%, #e6c2b1 52%, #ffffff 70%); }
  .brand-name { position: absolute; left: 0; right: 0; text-align: center; font-size: 17px; letter-spacing: 0.62em; text-indent: 0.62em; color: var(--ink); }
  .front-name { top: 452px; }
  .brand-tagline { position: absolute; left: 0; right: 0; text-align: center; font-size: 6px; letter-spacing: 0.9em; text-indent: 0.9em; color: var(--ink-soft); }
  .front-tagline { top: 483px; }

  /* back */
  .back-photo { position: absolute; inset: 0;
    background:
      radial-gradient(circle at 12% 10%, rgba(240,150,170,.55) 0 8%, transparent 20%),
      radial-gradient(circle at 85% 30%, rgba(240,150,170,.55) 0 7%, transparent 18%),
      radial-gradient(circle at 90% 62%, rgba(236,160,180,.5) 0 9%, transparent 22%),
      radial-gradient(circle at 95% 92%, rgba(235,120,150,.55) 0 6%, transparent 16%),
      radial-gradient(ellipse at 55% 55%, #ffffff 0 30%, #f7e6ee 60%, #efcfe0 100%); }
  .back-white { position: absolute; left: 0; bottom: 0; width: 100%; height: 55px; background: linear-gradient(100deg, #fff 0 45%, rgba(255,255,255,0) 75%); }
  .back-name { position: absolute; left: 60px; top: 288px; font-size: 9px; letter-spacing: 0.45em; color: var(--ink); }
  .back-tagline { position: absolute; left: 60px; top: 302px; font-size: 4px; letter-spacing: 0.55em; color: var(--ink-soft); }
  .contact-list { position: absolute; left: 70px; top: 318px; list-style: none; font-size: 12.5px; line-height: 16.6px; color: var(--ink); }
  .contact-list li { position: relative; padding-left: 16px; }
  .contact-list svg { position: absolute; left: 0; top: 4px; width: 9px; height: 9px; }
  .accent-bar { position: absolute; left: 0; top: 438px; width: 381px; height: 12px; background: var(--sky-bar); }

  /* inside */
  .inside-header { position: absolute; left: 0; top: 0; width: 505px; height: 178px;
    background: radial-gradient(ellipse at 15% 60%, #f0c7b2 0 25%, transparent 45%), linear-gradient(90deg, var(--peach) 0%, var(--peach-light) 100%); }
  .section-title { position: absolute; left: 194px; top: 74px; font-size: 32px; color: var(--ink); letter-spacing: 0.01em; }
  .service { position: absolute; left: 30px; width: 268px; }
  .service__head { display: flex; justify-content: space-between; align-items: center; height: 14px; }
  .service__name { font-family: "Nunito", sans-serif; font-weight: 700; font-size: 10.5px; color: var(--teal); }
  .service__price { background: var(--rose-pill); color: var(--white); font-family: "Nunito", sans-serif; font-weight: 600; font-size: 11px; line-height: 13px; padding: 0 6px; border-radius: 7px; }
  .service__text { margin-top: 3px; font-size: 9px; line-height: 11.6px; color: var(--ink-soft); text-align: justify; }
  .service--one { top: 188px; }
  .service--two { top: 262px; }
  .service--three { top: 380px; }
  .photo-ring { position: absolute; left: 352px; width: 126px; height: 126px; border-radius: 50%; border: 3px solid var(--ring); background: var(--white); padding: 5px; }
  .photo-ring__fill { width: 100%; height: 100%; border-radius: 50%; }
  .photo-ring--care { top: 199px; }
  .photo-ring--care .photo-ring__fill { background: radial-gradient(circle at 55% 45%, #f0d3c4 0 35%, #f6ece8 70%); }
  .photo-ring--products { top: 351px; }
  .photo-ring--products .photo-ring__fill { background: linear-gradient(90deg, #fff 0 12%, #f4c2c8 22% 45%, #fff 50%, #cfe9cf 56% 80%, #fff 90%); }
</style>
</head>
<body>

<section class="panel panel--front" aria-label="Voorzijde">
  <svg class="front-bg" viewBox="0 0 505 505" role="img" aria-label="Zachte bloesemfoto in lichtblauw en roze">
    <rect width="505" height="505" fill="var(--blush)"/>
    <polygon points="0,0 262,0 0,400" fill="var(--sky)"/>
    <polygon points="0,400 0,0 60,0 0,120" fill="#bfdde8" opacity=".6"/>
    <polygon points="0,505 0,430 190,505" fill="var(--blush-deep)"/>
    <polygon points="370,0 505,0 505,90" fill="#fbeaee"/>
  </svg>
  <div class="portrait-circle" role="img" aria-label="Portretfoto van een vrouw met opgestoken haar"></div>
  <p class="brand-name front-name">ATELIER VERANO</p>
  <p class="brand-tagline front-tagline">SCHOONHEIDSINSTITUUT</p>
</section>

<section class="panel panel--back" aria-label="Achterzijde">
  <div class="back-photo" role="img" aria-label="Roze kersenbloesem op takken, zacht vervaagd"></div>
  <div class="back-white"></div>
  <p class="back-name">ATELIER VERANO</p>
  <p class="back-tagline">SCHOONHEIDSINSTITUUT</p>
  <ul class="contact-list">
    <li><svg viewBox="0 0 10 10"><path d="M2 1 L4 3 L3 4 Q4 6 6 7 L7 6 L9 8 L8 9 Q3 9 1 2 Z" fill="var(--teal)"/></svg>0470 18 42 96</li>
    <li><svg viewBox="0 0 10 10"><circle cx="5" cy="5" r="4" fill="none" stroke="var(--teal)" stroke-width="1.4"/><path d="M1 5 H9 M5 1 Q2 5 5 9 Q8 5 5 1" fill="none" stroke="var(--teal)" stroke-width=".9"/></svg>www.atelierverano.be</li>
    <li><svg viewBox="0 0 10 10"><rect x="1" y="2.5" width="8" height="5.5" fill="none" stroke="var(--teal)" stroke-width="1.3"/><path d="M1 2.5 L5 6 L9 2.5" fill="none" stroke="var(--teal)" stroke-width="1"/></svg>info@atelierverano.be</li>
    <li><svg viewBox="0 0 10 10"><path d="M5 9.5 L2 5 A3 3 0 1 1 8 5 Z" fill="var(--teal)"/><circle cx="5" cy="4" r="1.1" fill="#fff"/></svg>Atelier Verano Schoonheidsinstituut<br>Lindelaan 14 (1e verdieping<br>Rozenhof) 9000 GENT</li>
  </ul>
  <div class="accent-bar"></div>
</section>

<section class="panel panel--inside" aria-label="Binnenzijde">
  <div class="inside-header" role="img" aria-label="Vrouw met open hand en vage bloesem op perzikkleurige achtergrond"></div>
  <h1 class="section-title">Gelaatsverzorging</h1>

  <article class="service service--one">
    <div class="service__head"><span class="service__name">Cosmetische Verzorging</span><span class="service__price">€30</span></div>
    <p class="service__text">Verzorging i.o.v. Dermatoloog.<br>De verzorging bestaat uit: oppervlakkige reiniging, verwijderen zwarte puntjes en onzuiverheden,zuiverend masker.</p>
  </article>

  <article class="service service--two">
    <div class="service__head"><span class="service__name">Hydratation Essentielle</span><span class="service__price">€15</span></div>
    <p class="service__text" style="margin-top:9px">Voor een gehydrateerde, volle en frisse huid.<br>Geschikt voor alle huidtypes.<br>De verzorging bestaat uit: epilatie wenkbrauwen, oppervlakkige reiniging, diepe reiniging, verwijderen van comedonen, massage van gelaat en décolleté, instituutmasker aangepast aan huidconditie, serum, dagcème, handmassage.</p>
  </article>

  <article class="service service--three">
    <div class="service__head"><span class="service__name">Flash Nettoyant</span><span class="service__price">€59 - 50 min.</span></div>
    <p class="service__text" style="margin-top:6px">Voor een gehydrateerde en comfortabele huid.<br>Voor alle huidtypes, bij een vermoeide huid met weinig uitstraling.<br>De verzorging bestaat uit: epilatie wenkbrauwen, oppervlakkige reiniging, diepe reiniging, cremmasker aangepast aan huidconditie, serum, dagcème, handmassage.</p>
  </article>

  <div class="photo-ring photo-ring--care"><div class="photo-ring__fill" role="img" aria-label="Glimlachende vrouw met hand tegen de wang"></div></div>
  <div class="photo-ring photo-ring--products"><div class="photo-ring__fill" role="img" aria-label="Twee flesjes gezichtslotion, roze en groen"></div></div>
</section>

</body>
</html>
```